Business Card Design

The Kestrel Lodge Inn is the most centrally located motel in Grafton.
We are the only family owned motel in Grafton.
Our colour scheme is blue, whiteand black.

I have uploaded a photo of our new rooms and the logo for you to use Thanks. Looking good

Industry/Entity Type

Motel

Contact Information for Business Card

The Kestrel Lodge Inn
Gareth & Lorna Pelling
Owner/Operators
14-16 Wexbury Lane, Grafton NSW 2460
Ph: 02 6617 3904
Email: thekestrellodgeinn@mailvista.example
reception@kestrellodgeinn.example.au
www.kestrellodgeinn.example.au

Colors
0392cd
0455a3

```html
<!DOCTYPE html>
<html lang="en">
<head>
<meta charset="utf-8">
<title>The Kestrel Lodge Inn – Business Card</title>
<link rel="stylesheet" href="https://fonts.googleapis.com/css2?family=Exo+2:wght@500;700&family=Open+Sans:wght@400;600&display=swap">
<style>
  :root {
    --blue-bright: #0392cd;
    --blue-deep: #0455a3;
    --blue-name: #2e3f9e;
    --ink: #2b2b2b;
    --grey: #8a8a8a;
    --rule: #d4d4d4;
    --card: #ffffff;
    --stage: #e4e4e4;
  }
  * { box-sizing: border-box; margin: 0; padding: 0; }
  html, body { width: 1200px; height: 900px; overflow: hidden; }
  body {
    background: radial-gradient(ellipse at 50% 45%, #f2f2f2 0%, var(--stage) 70%);
    font-family: "Open Sans", Arial, sans-serif;
    position: relative;
  }
  .card {
    position: absolute;
    left: 280px;
    width: 640px;
    height: 366px;
    background: var(--card);
    box-shadow: 0 6px 18px rgba(0,0,0,0.14);
    overflow: hidden;
  }
  .card--back { top: 60px; }
  .card--front { top: 474px; }
  .card__art { position: absolute; inset: 0; width: 100%; height: 100%; }

  .web-band {
    font-family: "Exo 2", Arial, sans-serif;
    font-weight: 500;
    font-size: 14px;
    letter-spacing: 1.5px;
    fill: #ffffff;
  }

  .brand { position: absolute; display: flex; align-items: center; gap: 10px; }
  .brand__dot {
    width: 30px; height: 30px; border-radius: 50%;
    background: var(--blue-deep);
    flex: none;
  }
  .brand__name {
    font-family: "Exo 2", Arial, sans-serif;
    font-weight: 700;
    font-size: 24px;
    color: var(--blue-deep);
    letter-spacing: 0.2px;
    white-space: nowrap;
  }
  .card--back .brand { left: 50%; top: 100px; transform: translateX(-50%); }
  .card--front .brand { left: 38px; top: 52px; }

  .logo-rule {
    position: absolute; left: 38px; top: 110px; width: 270px; height: 1px;
    background: var(--rule);
  }
  .person { position: absolute; right: 38px; top: 52px; text-align: right; }
  .person__name {
    font-family: "Exo 2", Arial, sans-serif;
    font-weight: 500;
    font-size: 18px;
    letter-spacing: 1px;
    color: var(--blue-name);
    text-transform: uppercase;
  }
  .person__role { font-size: 11px; color: var(--ink); margin-top: 2px; padding-top: 4px; border-top: 1px solid var(--rule); }
  .address {
    position: absolute; right: 38px; top: 112px; text-align: right;
    font-family: "Exo 2", Arial, sans-serif;
    font-weight: 500; font-size: 15px; line-height: 1.35; color: var(--ink);
  }
  .contacts { position: absolute; left: 38px; top: 122px; list-style: none; }
  .contacts__item {
    display: flex; align-items: center; gap: 8px;
    font-size: 10.5px; color: var(--ink); height: 19px;
  }
  .contacts__icon { width: 11px; height: 11px; flex: none; fill: var(--blue-deep); }
</style>
</head>
<body>

<section class="card card--back" aria-label="Business card back">
  <svg class="card__art" viewBox="0 0 640 366">
    <defs>
      <linearGradient id="bandBack" x1="0" y1="0" x2="1" y2="0">
        <stop offset="0" stop-color="#0455a3"/>
        <stop offset="0.5" stop-color="#0392cd"/>
        <stop offset="1" stop-color="#0455a3"/>
      </linearGradient>
      <linearGradient id="greyBack" x1="0" y1="0" x2="1" y2="0">
        <stop offset="0" stop-color="#bdbdbd" stop-opacity="0"/>
        <stop offset="0.6" stop-color="#8a8a8a"/>
        <stop offset="1" stop-color="#1e1e1e"/>
      </linearGradient>
      <path id="backTextLine" d="M0,340 C240,344 460,302 640,238"/>
    </defs>
    <path d="M180,286 C360,278 500,240 640,176 L640,196 C480,258 340,284 180,286 Z" fill="url(#greyBack)"/>
    <path d="M0,300 C240,304 460,262 640,198 L640,366 L0,366 Z" fill="url(#bandBack)"/>
    <text class="web-band" dominant-baseline="middle">
      <textPath href="#backTextLine" startOffset="50%" text-anchor="middle">www.kestrellodgeinn.example.au</textPath>
    </text>
  </svg>
  <div class="brand">
    <span class="brand__dot"></span>
    <span class="brand__name">The Kestrel Lodge Inn</span>
  </div>
</section>

<section class="card card--front" aria-label="Business card front">
  <svg class="card__art" viewBox="0 0 640 366">
    <defs>
      <linearGradient id="bandFront" x1="0" y1="1" x2="1" y2="0">
        <stop offset="0" stop-color="#0455a3"/>
        <stop offset="0.45" stop-color="#0392cd"/>
        <stop offset="1" stop-color="#0455a3"/>
      </linearGradient>
      <linearGradient id="greyFront" x1="0" y1="0" x2="1" y2="0">
        <stop offset="0" stop-color="#1e1e1e"/>
        <stop offset="0.5" stop-color="#8a8a8a"/>
        <stop offset="1" stop-color="#cfcfcf" stop-opacity="0"/>
      </linearGradient>
      <path id="frontTextLine" d="M40,352 Q320,246 640,194"/>
    </defs>
    <path d="M0,306 Q190,245 400,207 Q190,255 0,328 Z" fill="url(#greyFront)"/>
    <path d="M0,330 Q300,220 640,168 L640,216 Q330,262 70,366 L0,366 Z" fill="url(#bandFront)"/>
    <path d="M0,346 C20,352 40,360 56,366 L0,366 Z" fill="#1e1e1e"/>
    <text class="web-band" dominant-baseline="middle">
      <textPath href="#frontTextLine" startOffset="52%" text-anchor="middle">www.kestrellodgeinn.example.au</textPath>
    </text>
  </svg>

  <div class="brand">
    <span class="brand__dot"></span>
    <span class="brand__name">The Kestrel Lodge Inn</span>
  </div>
  <div class="logo-rule"></div>

  <div class="person">
    <p class="person__name">Gareth Pelling</p>
    <p class="person__role">Managing Director</p>
  </div>

  <p class="address">14-16 Wexbury Lane<br>Grafton NSW 2460</p>

  <ul class="contacts">
    <li class="contacts__item">
      <svg class="contacts__icon" viewBox="0 0 12 12"><path d="M2.5 1 L4.5 1 L5 3.5 L3.8 4.5 C4.5 6 6 7.5 7.5 8.2 L8.5 7 L11 7.5 L11 9.5 C11 10.5 10 11 9 11 C4.5 10.5 1.5 7.5 1 3 C1 2 1.5 1 2.5 1 Z"/></svg>
      <span>02 6617 3904</span>
    </li>
    <li class="contacts__item">
      <svg class="contacts__icon" viewBox="0 0 12 12"><path d="M6 0.5 C3.8 0.5 2.2 2.2 2.2 4.3 C2.2 7 6 11.5 6 11.5 C6 11.5 9.8 7 9.8 4.3 C9.8 2.2 8.2 0.5 6 0.5 Z M6 2.8 A1.5 1.5 0 1 1 6 5.8 A1.5 1.5 0 1 1 6 2.8 Z" fill-rule="evenodd"/></svg>
      <span>Grafton NSW 2460</span>
    </li>
    <li class="contacts__item">
      <svg class="contacts__icon" viewBox="0 0 12 12"><path d="M1 2.5 H11 V9.5 H1 Z M1.6 3 L6 6.5 L10.4 3 Z" fill-rule="evenodd"/></svg>
      <span>thekestrellodgeinn@mailvista.example</span>
    </li>
    <li class="contacts__item">
      <svg class="contacts__icon" viewBox="0 0 12 12"><path d="M1 2.5 H11 V9.5 H1 Z M1.6 3 L6 6.5 L10.4 3 Z" fill-rule="evenodd"/></svg>
      <span>reception@kestrellodgeinn.example.au</span>
    </li>
    <li class="contacts__item">
      <svg class="contacts__icon" viewBox="0 0 12 12"><path d="M6 0.5 A5.5 5.5 0 1 0 6 11.5 A5.5 5.5 0 1 0 6 0.5 Z M6 2 A4 4 0 1 1 6 10 A4 4 0 1 1 6 2 Z M5.3 1 H6.7 V11 H5.3 Z M1 5.3 H11 V6.7 H1 Z" fill-rule="evenodd"/></svg>
      <span>www.kestrellodgeinn.example.au</span>
    </li>
  </ul>
</section>

</body>
</html>
```